Business card for a Exhibition booth fabrication company

Hi. My company would like to change our corporate name card. We are an events and Exhibition stand builder company. We would like our corporate name card to resonate what we do. I need someone to create something unique that relates to the industry that I am in. The graphic designer should be creative to incorporate the elements of my industry and try to blend in well in the design of the card. Our aim is to ensure that we are unique and our card can look different from our competitors.
Updates

Target Market(s)

Marketing and events manager from all companies

Contact Information for Business Card

The business card should have the following details:
Name
Job Title
Email
Website

Colors

Designer to choose colors to be used in the design.

Requirements
Must have
• The card must be look something that is relevant to the service that I am providing. My website is: www.velmora-buildworks.com
• You can see my website to get more information on what service that I am doing
Nice to have
• On the back of my card, I would like to have a globe image with the incorporation of my company logo. This is to indicate that my services can be done in any part of the world.

```html
<!DOCTYPE html>
<html lang="en">
<head>
<meta charset="utf-8">
<title>Velmora Buildworks – Business Card</title>
<link rel="stylesheet" href="https://fonts.googleapis.com/css2?family=Josefin+Sans:wght@600&family=Baloo+2:wght@800&family=Arimo:wght@400;700&display=swap">
<style>
  :root {
    --paper: #ffffff;
    --maroon: #650111;
    --orange: #e8510d;
    --yellow: #f1bb14;
    --mist: #e6e6e6;
    --red: #e0262a;
    --ink: #2b2b2b;
    --black: #0b0b0b;
  }
  html, body {
    margin: 0;
    width: 1094px;
    height: 1200px;
    overflow: hidden;
    background: var(--paper);
  }
  .sheet { position: relative; width: 1094px; height: 1200px; }
  .card {
    position: absolute;
    left: 160px;
    width: 766px;
    height: 436px;
    background: var(--paper);
    box-shadow: 22px 22px 24px rgba(0,0,0,0.45);
  }
  .card--front { top: 110px; }
  .card--back { top: 620px; }
  .card svg { display: block; width: 100%; height: 100%; }
  .fill-maroon { fill: var(--maroon); }
  .fill-orange { fill: var(--orange); }
  .fill-yellow { fill: var(--yellow); }
  .fill-mist { fill: var(--mist); }
  .fill-black { fill: var(--black); }
  .fill-red { fill: var(--red); }
  .wordmark {
    font-family: "Josefin Sans", "Helvetica Neue", sans-serif;
    font-weight: 600;
    fill: var(--ink);
    letter-spacing: 2px;
  }
  .headline {
    font-family: "Baloo 2", "Arial Black", sans-serif;
    font-weight: 800;
    fill: var(--red);
  }
  .service {
    font-family: "Baloo 2", "Arial Black", sans-serif;
    font-weight: 800;
    fill: var(--maroon);
  }
  .contact {
    font-family: "Arimo", Arial, sans-serif;
    fill: var(--paper);
  }
  .person-name {
    font-family: "Arimo", Arial, sans-serif;
    font-weight: 700;
    fill: var(--maroon);
  }
  .person-title {
    font-family: "Arimo", Arial, sans-serif;
    font-weight: 400;
    fill: var(--ink);
    letter-spacing: 1px;
  }
  .stand-frame {
    fill: none;
    stroke: var(--maroon);
    stroke-width: 4;
    stroke-linejoin: round;
  }
  .stand-fascia { fill: var(--yellow); }
  .stand-counter { fill: var(--orange); }
</style>
</head>
<body>
<main class="sheet">

  <section class="card card--front" aria-label="Card front">
    <svg viewBox="0 0 1050 598" xmlns="http://www.w3.org/2000/svg">
      <path class="fill-mist" d="M915,0 Q860,95 822,195 L1050,300 L1050,0 Z"/>
      <path class="fill-yellow" d="M960,0 Q870,150 832,285 L1050,400 L1050,0 Z"/>
      <path class="fill-orange" d="M995,0 Q890,200 840,370 L1050,480 L1050,0 Z"/>
      <path class="fill-maroon" d="M1050,0 L1008,0 Q900,200 855,475 Q960,490 1050,535 Z"/>
      <g class="brand">
        <circle class="fill-red" cx="417" cy="268" r="36"/>
        <text class="wordmark" x="417" y="362" font-size="31" text-anchor="middle">VELMORA BUILDWORKS</text>
      </g>
    </svg>
  </section>

  <section class="card card--back" aria-label="Card back">
    <svg viewBox="0 0 1050 598" xmlns="http://www.w3.org/2000/svg">
      <path class="fill-mist" d="M562,0 L612,0 Q672,110 705,198 L600,215 Z"/>
      <path class="fill-yellow" d="M522,0 L572,0 Q660,160 695,288 L600,305 Z"/>
      <path class="fill-orange" d="M478,0 L528,0 Q640,200 685,372 L590,400 Z"/>
      <path class="fill-maroon" d="M0,0 L480,0 Q620,230 670,475 Q480,500 395,598 L0,598 Z"/>

      <rect class="fill-yellow" x="22" y="133" width="495" height="90" rx="45"/>
      <text class="headline" x="270" y="195" font-size="50" text-anchor="middle">Velmora Buildworks</text>

      <path class="fill-yellow" d="M0,388 L430,388 Q462,388 462,420 Q462,452 430,452 L0,452 Z"/>
      <text class="service" x="12" y="432" font-size="33">Exhibition booth fabrication</text>

      <path class="fill-black" d="M0,460 L285,460 Q310,460 310,482 Q310,505 285,505 L0,505 Z"/>
      <text class="contact" x="10" y="489" font-size="18">hello@velmora-buildworks.com</text>

      <g class="brand">
        <circle class="fill-red" cx="895" cy="85" r="22"/>
        <text class="wordmark" x="895" y="134" font-size="16" text-anchor="middle">VELMORA BUILDWORKS</text>
      </g>

      <g class="stand" role="img" aria-label="Outline of an exhibition stand">
        <rect class="stand-fascia" x="800" y="172" width="200" height="20"/>
        <path class="stand-frame" d="M806,192 L806,290 M994,192 L994,290 M780,290 L1020,290"/>
        <rect class="stand-counter" x="860" y="250" width="80" height="40"/>
      </g>

      <text class="person-name" x="1020" y="345" font-size="26" text-anchor="end">Daniel Okafor</text>
      <text class="person-title" x="1020" y="372" font-size="16" text-anchor="end">Project Director</text>

      <path class="fill-black" d="M1050,450 L760,450 Q740,450 740,470 Q740,490 760,490 L1050,490 Z"/>
      <text class="contact" x="780" y="476" font-size="18">www.velmora-buildworks.com</text>
    </svg>
  </section>

</main>
</body>
</html>
```